Falkrin homes and renovations business card design.

Would like some new card designs utilizing my new logo that look professional. I am open to different colors on the logo or utilize the same ones we have. I like the original concept but would like to see some fresh ideas and build on what we have already done.

Target Market(s)

Custom home building industry, Real estate sales, Renovation projects.

Industry/Entity Type

Home Builder

Contact Information for Business Card

Falkrin Homes and Renovations
2871 96th Avenue
Frank, Alberta
T2R3W8
Home : 403- 718-4063 Cell: 403- 294-5170

My info is : Dax Falkrin, President and CEO
email: falkrinhomes@maildrop-example.net
Website: falkrinhomes-example.com
websit

Requirements
Must have
• Must Use my new logo design. I am open to different colors on the logo or utilize the same ones in the existing design. I can upload the original logo design if needed.

```html
<!DOCTYPE html>
<html lang="en">
<head>
<meta charset="utf-8">
<title>Falkrin Homes and Renovations – Business Card</title>
<link rel="stylesheet" href="https://fonts.googleapis.com/css2?family=Open+Sans:wght@400;600&family=Montserrat:wght@400;500&display=swap">
<style>
  :root {
    --backdrop: #7a5a40;
    --card-black: #050505;
    --gold: #c69a3c;
    --gold-dark: #9c7423;
    --yellow: #ffcc00;
    --text-light: #e6e6e6;
    --text-muted: #cfcfcf;
    --ink: #111111;
  }
  * { box-sizing: border-box; margin: 0; padding: 0; }
  html, body {
    width: 1200px; height: 987px; overflow: hidden;
    background: var(--backdrop);
    font-family: "Open Sans", Arial, sans-serif;
  }
  .stage { position: relative; width: 1200px; height: 987px; }
  .card {
    position: absolute; left: 293px; width: 615px; height: 352px;
    box-shadow: 0 4px 10px rgba(0,0,0,.35);
    overflow: hidden;
  }
  .card-front { top: 130px; background: var(--card-black); }
  .card-back { top: 505px; background: var(--yellow); }

  .brand { position: absolute; right: 31px; top: 100px; text-align: right; color: var(--gold); font-family: "Montserrat", Arial, sans-serif; font-weight: 400; }
  .brand-name { font-size: 37px; letter-spacing: 1px; line-height: 1; }
  .brand-tagline { font-size: 13px; letter-spacing: .6px; margin-top: 6px; }

  .person { position: absolute; left: 34px; top: 143px; }
  .person-name { color: var(--gold); font-size: 21px; font-weight: 600; letter-spacing: .3px; }
  .person-title { color: var(--text-muted); font-size: 16px; margin-top: 2px; }

  .divider { position: absolute; left: 34px; width: 550px; top: 215px; height: 1px; background: #8a8a8a; }

  .contacts { position: absolute; left: 34px; top: 226px; list-style: none; }
  .contacts li { display: flex; align-items: center; height: 23.5px; color: var(--text-light); font-size: 15px; }
  .contacts svg { width: 15px; height: 15px; margin-right: 13px; fill: var(--gold); flex: none; }

  .address { position: absolute; right: 31px; top: 250px; text-align: right; color: var(--text-light); font-size: 14.5px; line-height: 20.5px; font-style: normal; }
  .address strong { font-weight: 600; }

  .band { position: absolute; left: 0; bottom: 0; width: 615px; height: 16px; }

  .back-brand { position: absolute; left: 0; right: 0; top: 110px; text-align: center; color: var(--ink); font-family: "Montserrat", Arial, sans-serif; font-weight: 500; }
  .back-brand-name { font-size: 64px; letter-spacing: 3px; line-height: 1; }
  .back-brand-tagline { font-size: 19px; letter-spacing: 2px; margin-top: 10px; }
  .back-url { position: absolute; left: 0; right: 0; top: 295px; text-align: center; color: var(--ink); font-size: 15px; letter-spacing: 3.6px; }
</style>
</head>
<body>
<main class="stage">
  <section class="card card-front">
    <div class="brand">
      <div class="brand-name">FALKRIN</div>
      <div class="brand-tagline">HOMES AND RENOVATIONS</div>
    </div>

    <div class="person">
      <div class="person-name">DAX FALKRIN</div>
      <div class="person-title">CEO&amp;Founder</div>
    </div>

    <div class="divider"></div>

    <ul class="contacts">
      <li><svg viewBox="0 0 16 16"><path d="M3.5 1.5l2.5 3-1.5 1.8c.9 2 2.4 3.5 4.4 4.4l1.8-1.5 3 2.5-1.6 2.3C7.5 13.8 2.2 8.5 1.2 3.1z"/></svg>403- 718-4063</li>
      <li><svg viewBox="0 0 16 16"><path d="M4.5 0h7a1 1 0 0 1 1 1v14a1 1 0 0 1-1 1h-7a1 1 0 0 1-1-1V1a1 1 0 0 1 1-1zm.7 2v10.5h5.6V2zM8 13.3a.9.9 0 1 0 0 1.8.9.9 0 0 0 0-1.8z"/></svg>403- 294-5170</li>
      <li><svg viewBox="0 0 16 16"><path d="M1 3.5h14v9H1zm1.2 1.1L8 9l5.8-4.4z"/></svg>info@falkrinhomes-example.com</li>
      <li><svg viewBox="0 0 16 16"><circle cx="8" cy="8" r="7"/></svg>falkrinhomes-example.com</li>
    </ul>

    <address class="address">
      <strong>Falkrin homes &amp; Renovations</strong><br>
      2871 96th Avenue<br>
      Frank, Alberta, T2R3W8
    </address>

    <svg class="band" viewBox="0 0 615 16" preserveAspectRatio="none" aria-hidden="true">
      <defs>
        <linearGradient id="band-gold" x1="0" x2="1">
          <stop offset="0" stop-color="var(--gold-dark)"/>
          <stop offset=".6" stop-color="var(--gold)"/>
          <stop offset="1" stop-color="var(--gold-dark)"/>
        </linearGradient>
      </defs>
      <rect x="0" y="3" width="406" height="13" fill="url(#band-gold)"/>
      <polygon points="400,0 410,0 404,16 394,16" fill="var(--card-black)"/>
      <polygon points="410,2 615,2 615,16 404,16" fill="var(--yellow)"/>
    </svg>
  </section>

  <section class="card card-back">
    <div class="back-brand">
      <div class="back-brand-name">FALKRIN</div>
      <div class="back-brand-tagline">HOMES AND RENOVATIONS</div>
    </div>
    <div class="back-url">www.falkrinhomes-example.com</div>
  </section>
</main>
</body>
</html>
```